Stationery Design Project

Hi All,

We need you to design stationary for a new Business and Accounting Advisory Firm. We have already got the logo designed and it is attached. If you could also if possible, match the fonts in your design to that on the logo’s provided.

What we need:
- Business Card
- A4 Letter head
- A4 Folders
- PPT template (Title page and regular page)

And what ever else you want to throw in.

We are in the process of getting the web site designed, however below is a list of websites which we like which will give you an understanding of the style that we are going for.

- plivant.example
- moldrabay.example
- tarvenhook.example
- quillorbank.example

I look forward to your seeing your design.
Updates

Hi All,

I have just realised that I forgot that i need to include a Sworn Ledgerkeepers image on the letter head, please find attaced as File 1. Could you please have this image in the bottom left header.

Regards,

Marcus

Industry/Entity Type

Business

Requirements
Must have
• Outputs:
- Documents ready to print
- Generic editable information
- Pdf copies of the documents
- Word version of letterhead

```html
<!DOCTYPE html>
<html lang="en">
<head>
<meta charset="utf-8">
<title>Brenholt Partners — Stationery</title>
<link rel="stylesheet" href="https://fonts.googleapis.com/css2?family=Crimson+Text:wght@400;600&family=Open+Sans:wght@400;600&family=Cormorant+Garamond:ital,wght@1,500&display=swap">
<style>
  :root {
    --page-bg: #f3eee6;
    --paper: #ffffff;
    --blue-deep: #2a55d6;
    --blue-mid: #3a86dc;
    --teal: #4fe0dc;
    --orange: #ff7a12;
    --amber: #ffb62a;
    --ink-blue: #2b4fc9;
    --ink-dark: #222222;
    --badge-red: #b8141c;
    --shadow: 0 6px 14px rgba(0,0,0,.35);
  }
  * { box-sizing: border-box; margin: 0; padding: 0; }
  html, body { width: 1200px; height: 1089px; overflow: hidden; }
  body { background: var(--page-bg); position: relative; font-family: "Open Sans", Arial, sans-serif; }

  .item { position: absolute; background: var(--paper); box-shadow: var(--shadow); overflow: hidden; }
  .item svg.art { position: absolute; inset: 0; width: 100%; height: 100%; }

  .label {
    position: absolute; font-family: "Cormorant Garamond", Georgia, serif;
    font-style: italic; font-weight: 500; font-size: 30px; color: var(--ink-dark);
    white-space: nowrap;
  }

  .brand { position: absolute; display: flex; align-items: center; gap: 10px; }
  .brand-dot { border-radius: 50%; background: var(--orange); flex: none; }
  .brand-text { display: flex; flex-direction: column; line-height: 1; }
  .brand-name { font-family: "Crimson Text", Georgia, serif; font-weight: 400; color: var(--ink-blue); white-space: nowrap; }
  .brand-tag { font-family: "Open Sans", Arial, sans-serif; color: var(--ink-blue); letter-spacing: .32em; white-space: nowrap; margin-top: 3px; }

  .credential { position: absolute; display: flex; align-items: center; gap: 5px; }
  .credential-badge { border-radius: 50%; background: var(--badge-red); flex: none; }
  .credential-text { font-family: "Open Sans", Arial, sans-serif; font-weight: 600; color: var(--ink-dark); line-height: 1.05; }

  /* Letterhead */
  .letterhead { left: 145px; top: 9px; width: 406px; height: 566px; }
  .letterhead .rule { position: absolute; left: 118px; top: 278px; width: 170px; height: 1px; background: #b9c8e6; }

  /* Business cards */
  .card-front { left: 462px; top: 138px; width: 152px; height: 98px; background: linear-gradient(90deg, var(--orange), var(--amber)); }
  .card-back { left: 600px; top: 168px; width: 170px; height: 108px; z-index: 2; }

  /* Folder */
  .folder { left: 790px; top: 58px; width: 390px; height: 594px; }

  /* Envelopes */
  .envelope-front { left: 100px; top: 640px; width: 462px; height: 262px; }
  .envelope-rear { left: 592px; top: 722px; width: 490px; height: 272px; }
</style>
</head>
<body>

  <!-- Letterhead -->
  <section class="item letterhead" aria-label="A4 letterhead">
    <svg class="art" viewBox="0 0 406 566" preserveAspectRatio="none">
      <defs>
        <linearGradient id="lh-band" x1="0" x2="1">
          <stop offset="0" stop-color="var(--blue-deep)"/><stop offset=".55" stop-color="var(--blue-mid)"/><stop offset="1" stop-color="var(--teal)"/>
        </linearGradient>
        <linearGradient id="lh-foot" x1="0" x2="1">
          <stop offset="0" stop-color="var(--blue-mid)"/><stop offset="1" stop-color="var(--teal)"/>
        </linearGradient>
      </defs>
      <rect x="0" y="0" width="406" height="82" fill="url(#lh-band)"/>
      <path d="M352 0 C362 25 364 55 360 82 L372 82 C376 55 374 25 364 0Z" fill="var(--orange)"/>
      <path d="M364 0 C374 25 376 55 372 82 L380 82 C384 55 382 25 372 0Z" fill="var(--amber)"/>
      <path d="M130 566 C240 520 340 490 406 462 L406 566Z" fill="url(#lh-foot)"/>
      <path d="M150 566 C250 515 340 480 406 448 L406 462 C340 490 240 525 130 566Z" fill="var(--amber)"/>
      <path d="M138 566 C245 518 340 485 406 455 L406 462 C340 490 240 522 130 566Z" fill="var(--orange)"/>
    </svg>
    <div class="brand" style="left:14px; top:14px;">
      <span class="brand-dot" style="width:40px;height:40px;"></span>
      <span class="brand-text">
        <span class="brand-name" style="font-size:28px;">Brenholt Partners</span>
        <span class="brand-tag" style="font-size:10px;">Business Advisors</span>
      </span>
    </div>
    <div class="rule"></div>
    <div class="credential" style="left:312px; top:534px;">
      <span class="credential-badge" style="width:22px;height:22px;"></span>
      <span class="credential-text" style="font-size:7px;">Sworn<br>Ledgerkeeper</span>
    </div>
  </section>
  <div class="label" style="left:4px; top:478px;">Letter head</div>

  <!-- Business cards -->
  <div class="label" style="left:588px; top:78px;">Business Card</div>
  <section class="item card-front" aria-label="Business card front">
    <div class="brand" style="left:28px; top:33px;">
      <span class="brand-dot" style="width:30px;height:30px;background:var(--blue-mid);"></span>
    </div>
  </section>
  <section class="item card-back" aria-label="Business card back">
    <svg class="art" viewBox="0 0 178 108" preserveAspectRatio="none">
      <defs>
        <linearGradient id="bc-foot" x1="0" x2="1">
          <stop offset="0" stop-color="var(--blue-deep)"/><stop offset="1" stop-color="var(--blue-mid)"/>
        </linearGradient>
      </defs>
      <path d="M0 108 L0 100 C70 100 140 80 178 40 L178 108Z" fill="url(#bc-foot)"/>
      <path d="M150 0 C175 30 170 70 120 95 C165 72 185 30 160 0Z" fill="var(--amber)"/>
      <path d="M160 0 C185 30 178 62 150 85 L178 60 L178 0Z" fill="var(--blue-mid)"/>
    </svg>
    <div class="brand" style="left:10px; top:12px; gap:5px;">
      <span class="brand-dot" style="width:18px;height:18px;"></span>
      <span class="brand-text">
        <span class="brand-name" style="font-size:12px;">Brenholt Partners</span>
        <span class="brand-tag" style="font-size:5px;">Business Advisors</span>
      </span>
    </div>
    <div class="credential" style="left:10px; top:70px;">
      <span class="credential-badge" style="width:16px;height:16px;"></span>
      <span class="credential-text" style="font-size:5.5px;">Sworn<br>Ledgerkeeper</span>
    </div>
  </section>

  <!-- A4 Folder -->
  <section class="item folder" aria-label="A4 presentation folder">
    <svg class="art" viewBox="0 0 455 594" preserveAspectRatio="none">
      <defs>
        <linearGradient id="fd-body" x1="0" x2="1">
          <stop offset="0" stop-color="var(--blue-deep)"/><stop offset=".55" stop-color="var(--blue-mid)"/><stop offset="1" stop-color="var(--teal)"/>
        </linearGradient>
        <linearGradient id="fd-edge" x1="0" x2="1">
          <stop offset="0" stop-color="var(--teal)"/><stop offset="1" stop-color="var(--blue-deep)"/>
        </linearGradient>
      </defs>
      <rect width="455" height="594" fill="url(#fd-body)"/>
      <path d="M405 0 C440 200 430 420 345 594 L455 594 L455 0Z" fill="url(#fd-edge)"/>
      <path d="M400 0 C432 200 422 420 335 594 L358 594 C440 420 448 200 418 0Z" fill="var(--orange)"/>
      <path d="M412 0 C442 200 434 420 350 594 L358 594 C440 420 448 200 418 0Z" fill="var(--amber)"/>
    </svg>
    <div class="brand" style="left:22px; top:184px;">
      <span class="brand-dot" style="width:54px;height:54px;"></span>
      <span class="brand-text">
        <span class="brand-name" style="font-size:29px;">Brenholt Partners</span>
        <span class="brand-tag" style="font-size:10px;">Business Advisors</span>
      </span>
    </div>
  </section>
  <div class="label" style="left:608px; top:620px;">A4 Folders</div>

  <!-- Envelope front -->
  <section class="item envelope-front" aria-label="Envelope front">
    <svg class="art" viewBox="0 0 462 262" preserveAspectRatio="none">
      <defs>
        <linearGradient id="ev-flap" x1="0" x2="1">
          <stop offset="0" stop-color="var(--orange)"/><stop offset="1" stop-color="var(--amber)"/>
        </linearGradient>
        <linearGradient id="ev-blue" x1="0" x2="1">
          <stop offset="0" stop-color="var(--blue-deep)"/><stop offset="1" stop-color="var(--teal)"/>
        </linearGradient>
      </defs>
      <rect width="462" height="42" fill="url(#ev-flap)"/>
      <rect x="356" y="42" width="32" height="220" fill="url(#ev-blue)"/>
      <rect x="392" y="42" width="30" height="220" fill="url(#ev-flap)"/>
      <path d="M0 150 C30 200 70 240 120 262 L0 262Z" fill="url(#ev-flap)"/>
    </svg>
    <div class="brand" style="left:18px; top:62px;">
      <span class="brand-dot" style="width:46px;height:46px;"></span>
      <span class="brand-text">
        <span class="brand-name" style="font-size:27px;">Brenholt Partners</span>
        <span class="brand-tag" style="font-size:10px;">Business Advisors</span>
      </span>
    </div>
  </section>
  <div class="label" style="left:54px; top:922px;">envelope front</div>

  <!-- Envelope rear -->
  <section class="item envelope-rear" aria-label="Envelope rear">
    <svg class="art" viewBox="0 0 490 272" preserveAspectRatio="none">
      <defs>
        <linearGradient id="er-flap" x1="0" x2="1">
          <stop offset="0" stop-color="var(--orange)"/><stop offset="1" stop-color="var(--amber)"/>
        </linearGradient>
      </defs>
      <rect width="490" height="58" fill="url(#er-flap)"/>
      <path d="M0 200 C40 240 100 262 170 272 L0 272Z" fill="url(#er-flap)"/>
    </svg>
    <div class="brand" style="left:300px; top:212px; gap:6px;">
      <span class="brand-dot" style="width:26px;height:26px;"></span>
      <span class="brand-text">
        <span class="brand-name" style="font-size:16px;">Brenholt Partners</span>
        <span class="brand-tag" style="font-size:6px;">Business Advisors</span>
      </span>
    </div>
  </section>
  <div class="label" style="left:660px; top:1030px;">envelope rear</div>

</body>
</html>
```